Website for a Psychologist in Private Practice

I need a cool web design for my website: www.drkalvoric.com. I would like it to look professional. Keep all the current content and add: Space for video; radio spots (see Silver Cedar Tunes Logo below for those); Quick Inquiry; Friendora link; 5 star rating on Rivo; a map; reviews from former patients. I am open to suggestions.

Target Market(s)

Those seeking individual and marital counseling.

Industry/Entity Type

Mental Health

Number of Pages Required

1 page

Font styles to use
Sans Serif
Other font styles liked:
• I'm open but no hard to read script

Requirements
Must have
• All the content on my home page with link for video and radio spots. List services and degrees and expertices (pics not necessary).
Nice to have
• A video of me and radio conversations (logo of Silver Cedar Tunes radio attached).
Should not have
• Cartoons, comedy, etc.... I don't need pictures of services (marital, depression, etc...) Just list those.

```html
<!DOCTYPE html>
<html lang="en">
<head>
<meta charset="utf-8">
<title>Dr. Mara K. Kalvoric — Individual and Marital Counseling</title>
<link rel="stylesheet" href="https://fonts.googleapis.com/css2?family=Lato:wght@400;700&family=Raleway:wght@500;600;700&family=Playball&display=swap">
<style>
:root{
  --blue:#2f86c4;
  --blue-dark:#2371aa;
  --gold:#c8ab4e;
  --gold-soft:#d6bf6d;
  --ink:#2d2d2d;
  --text:#444;
  --muted:#777;
  --nav:#2f2f2f;
  --line:#e2e2e2;
  --card:#e9e9e9;
  --paper:#ffffff;
  --soft:#f5f5f5;
}
*{box-sizing:border-box;margin:0;padding:0}
html,body{width:1200px;height:2667px;overflow:hidden;background:var(--paper)}
body{position:relative;font-family:"Lato",Arial,sans-serif;color:var(--text)}
.abs{position:absolute}

/* header */
.site-header{left:0;top:0;width:1200px;height:114px;background:var(--soft)}
.brand{left:78px;top:38px;font-family:"Raleway",Arial,sans-serif;font-weight:600;font-size:34px;color:var(--gold);letter-spacing:.5px}
.contact-pill{top:40px;height:42px;border:1px solid var(--line);border-radius:21px;background:#fff;display:flex;align-items:center;gap:10px;padding:0 22px;font-size:16px;color:var(--ink)}
.contact-pill b{font-weight:700}
.contact-pill svg{width:18px;height:18px}
.pill-mail{left:570px;width:306px}
.pill-phone{left:887px;width:233px}

/* nav */
.main-nav{left:0;top:114px;width:1200px;height:62px;background:var(--nav);display:flex;align-items:center;justify-content:space-between;padding:0 78px 0 80px}
.main-nav a{font-family:"Raleway",Arial,sans-serif;font-weight:700;font-size:18px;color:#fff;text-decoration:none;padding:10px 9px}
.main-nav a.active{background:var(--blue)}

/* hero */
.hero{left:0;top:176px;width:1200px;height:487px;background:linear-gradient(90deg,#dcd9cf 0%,#cfcbc0 35%,#e8eef3 55%,#b9a38c 80%,#6d6f86 100%)}
.hero-caption{left:0;top:588px;width:1200px;height:72px;background:rgba(70,70,70,.72);color:#fff;font-family:"Raleway",Arial,sans-serif;font-weight:600;font-size:29px;text-align:center;line-height:72px}
.hero-arrow{top:366px;width:32px;height:32px;background:#222;display:flex;align-items:center;justify-content:center}
.hero-arrow svg{width:14px;height:14px}

/* about */
.script-title{font-family:"Playball",cursive;font-size:38px;color:var(--ink)}
.script-title span{color:var(--gold)}
.title-rule{height:3px;background:var(--blue)}
.about-title{left:80px;top:732px}
.about-rule{left:80px;top:793px;width:106px}
.about-text{left:82px;top:814px;width:682px;font-size:14.5px;line-height:26px;color:var(--ink)}
.about-text b{font-weight:700}
.value{top:932px;width:330px;display:flex;gap:16px}
.value-icon{width:78px;height:78px;border:2px solid var(--blue);border-radius:50%;flex:none;display:flex;align-items:center;justify-content:center}
.value-icon svg{width:40px;height:40px}
.value h3{font-family:"Raleway",Arial,sans-serif;font-weight:500;font-size:21px;color:var(--blue);margin:4px 0 4px;padding-bottom:4px;border-bottom:1px dotted #ccc;display:inline-block}
.value p{font-size:14.5px;line-height:20px;color:var(--ink)}
.value-philosophy{left:80px}
.value-mission{left:452px}

.inquiry{left:807px;top:743px;width:314px;height:332px;background:#ececec;border-radius:4px}
.inquiry h2{height:48px;background:var(--blue);color:#fff;border-radius:4px 4px 0 0;font-family:"Raleway",Arial,sans-serif;font-weight:700;font-size:19px;line-height:48px;padding-left:25px}
.inquiry form{padding:16px 23px 0 23px}
.field{width:268px;height:34px;background:#fff;border:1px solid #d6d6d6;margin-bottom:8px;font-size:13px;color:#777;padding:0 10px;line-height:34px;position:relative}
.field.select::after{content:"";position:absolute;right:10px;top:14px;border:6px solid transparent;border-top:7px solid var(--gold)}
.field.msg{height:66px;line-height:20px;padding-top:6px}
.submit{display:inline-block;margin-top:10px;background:var(--blue);color:#fff;font-weight:700;font-size:15px;padding:11px 18px;border-radius:2px}

/* sessions & video */
.sessions{left:0;top:1152px;width:600px;height:356px;background:linear-gradient(120deg,#cdb45c,#d8c27a 50%,#c4a84e);text-align:center;color:#fff}
.sessions-icon{margin:22px auto 0;width:52px;height:52px}
.sessions h2{font-family:"Raleway",Arial,sans-serif;font-weight:600;font-size:35px;margin-top:8px}
.session-list{display:grid;grid-template-columns:140px 180px;column-gap:20px;row-gap:9px;width:340px;margin:16px auto 0;text-align:left;font-size:13.5px;color:#222;list-style:none}
.session-list li{display:flex;align-items:center;gap:8px}
.session-list svg{width:13px;height:13px;flex:none}
.get-started{display:inline-block;margin-top:26px;border:2px solid #fff;padding:7px 32px;font-size:17px;font-weight:700}
.video{left:600px;top:1152px;width:600px;height:356px;background:linear-gradient(135deg,#5f9fd0,#4f90c6 50%,#6aa6d4);text-align:center;color:#fff}
.video p{margin-top:107px;font-size:17px}
.play{margin:30px auto 0;width:56px;height:40px;background:#fff;border-radius:6px;display:flex;align-items:center;justify-content:center}
.play svg{width:18px;height:18px}
.video h3{margin-top:22px;font-size:17px;font-weight:700}

/* expertise */
.expertise-title{left:0;width:1200px;top:1548px;text-align:center}
.expertise-rule{left:546px;top:1612px;width:108px}
.card{width:252px;height:215px;background:linear-gradient(135deg,#e4e4e4 0%,#e4e4e4 50%,#ededed 50%,#ececec 100%);text-align:center;overflow:hidden}
.card svg.ico{margin-top:26px;width:54px;height:54px}
.card h3{font-family:"Lato",Arial,sans-serif;font-weight:700;font-size:14.5px;color:#222;margin-top:14px}
.card p{font-size:13.5px;line-height:19px;color:#333;margin:12px auto 0;width:200px}
.card .corner{position:absolute;right:0;bottom:0;width:0;height:0;border-left:36px solid transparent;border-bottom:36px solid var(--gold)}
.card .plus{position:absolute;right:6px;bottom:2px;color:#fff;font-size:12px;font-weight:700}
.c1{left:80px}.c2{left:343px}.c3{left:606px}.c4{left:869px}
.r1{top:1653px}.r2{top:1882px}

/* radio */
.radio{left:0;top:2160px;width:1200px;height:293px;background:var(--soft)}
.radio-title{left:0;width:1200px;top:2196px;text-align:center}
.radio-rule{left:546px;top:2260px;width:108px}
.quote{left:150px;top:2287px;width:900px;text-align:center;font-style:italic;font-size:14px;line-height:22px;color:#333}
.quote-mark{font-family:Georgia,serif;font-size:34px;color:var(--gold-soft);font-style:normal;vertical-align:-10px;margin-right:6px}
.quote-name{left:0;width:1200px;top:2372px;text-align:center;font-weight:700;font-size:17px;color:var(--gold)}
.radio-arrow{top:2300px;width:16px;height:28px}

/* footer */
.footer{left:0;top:2453px;width:1200px;height:178px;background:linear-gradient(180deg,#3a3a3a,#2d2d2d)}
.donate{left:350px;top:2476px;display:flex;align-items:center;gap:14px;color:#fff;font-weight:700;font-size:17px}
.badge{width:92px;height:40px;background:#fff;border-radius:2px}
.foot-row{top:2560px;display:flex;align-items:center;gap:12px;color:#fff;font-size:14px}
.foot-row svg{width:20px;height:20px}
.f-addr{left:184px}.f-phone{left:630px}.f-mail{left:830px}
.copyright{left:0;top:2631px;width:1200px;height:36px;background:var(--blue);color:#fff;font-size:13px;text-align:center;line-height:36px}
</style>
</head>
<body>

<header class="site-header abs"></header>
<div class="brand abs">Dr. Mara K. Kalvoric</div>
<div class="contact-pill pill-mail abs">
  <svg viewBox="0 0 20 20" fill="none" stroke="#c8ab4e" stroke-width="1.6"><rect x="2" y="4" width="16" height="12" rx="1"/><path d="M2 5l8 6 8-6"/></svg>
  Email Us <b>mk@drkalvoric.com</b>
</div>
<div class="contact-pill pill-phone abs">
  <svg viewBox="0 0 20 20" fill="none" stroke="#c8ab4e" stroke-width="1.6"><path d="M5 2l3 4-2 2c1 2 3 4 5 5l2-2 4 3-2 3C9 17 3 11 3 4z"/></svg>
  Call Us <b>(555) 214 3089</b>
</div>

<nav class="main-nav abs">
  <a class="active">HOME</a><a>BIO</a><a>MY EXPERTISE</a><a>SESSIONS</a><a>RESOURCES</a><a>CONTACT ME</a>
</nav>

<div class="hero abs" role="img" aria-label="Photo of a counselor listening to a young male client in a bright office"></div>
<div class="hero-arrow abs" style="left:6px"><svg viewBox="0 0 10 10"><path d="M7 1L3 5l4 4" fill="none" stroke="#fff" stroke-width="2"/></svg></div>
<div class="hero-arrow abs" style="left:1162px"><svg viewBox="0 0 10 10"><path d="M3 1l4 4-4 4" fill="none" stroke="#fff" stroke-width="2"/></svg></div>
<div class="hero-caption abs">I Provide individual and marital counseling</div>

<h2 class="script-title about-title abs">About <span>Dr. Mara K. Kalvoric</span></h2>
<div class="title-rule about-rule abs"></div>
<p class="about-text abs">While I acknowledge the importance of my education, I also appreciate the role my experiences have played in allowing me to relate so well to others. Allow me to share those I feel are most relevant with you.I survived an abusive childhood that my mother and sister unfortunately did not &nbsp;…… &nbsp;<b>Read More</b></p>

<div class="value value-philosophy abs">
  <div class="value-icon"><svg viewBox="0 0 40 40" fill="#c8ab4e"><path d="M20 5c-8 0-13 6-13 13 0 4 2 6 3 8v9h13v-5h4c2 0 3-1 3-3v-4h3l-3-6C30 10 26 5 20 5z"/><circle cx="20" cy="17" r="4" fill="#fff"/></svg></div>
  <div><h3>My Philosophy</h3><p>Lorem ipsum dolor sit amet,conse ctetuer adipiscing elit,</p></div>
</div>
<div class="value value-mission abs">
  <div class="value-icon"><svg viewBox="0 0 40 40" fill="none" stroke-width="3"><circle cx="20" cy="20" r="14" stroke="#c8ab4e"/><circle cx="20" cy="20" r="8" stroke="#2f86c4"/><circle cx="20" cy="20" r="2.5" fill="#c8ab4e" stroke="none"/><path d="M20 20l12-12" stroke="#2f86c4"/></svg></div>
  <div><h3>My Mission</h3><p>Lorem ipsum dolor sit amet,conse ctetuer adipiscing elit,</p></div>
</div>

<section class="inquiry abs">
  <h2>QUICK INQUIRY</h2>
  <form>
    <div class="field">Full Name</div>
    <div class="field">Phone Number</div>
    <div class="field select">Email</div>
    <div class="field msg">Message</div>
    <span class="submit">SUBMIT</span>
  </form>
</section>

<section class="sessions abs" role="img" aria-label="Gold-toned photo of a counseling session behind the list of session types">
  <svg class="sessions-icon" viewBox="0 0 52 52" fill="#fff"><circle cx="20" cy="12" r="9"/><path d="M4 48c0-14 7-22 16-22 4 0 7 1 9 3l-6 9 4 3 13-16 3 2-14 21H4z"/></svg>
  <h2>Type of Sessions i Provide</h2>
  <ul class="session-list">
    <li><svg viewBox="0 0 12 12"><path d="M1 6l3 3 7-7" fill="none" stroke="#222" stroke-width="2"/></svg>Individual Sessions</li>
    <li><svg viewBox="0 0 12 12"><path d="M1 6l3 3 7-7" fill="none" stroke="#222" stroke-width="2"/></svg>Divorce Mediation</li>
    <li><svg viewBox="0 0 12 12"><path d="M1 6l3 3 7-7" fill="none" stroke="#222" stroke-width="2"/></svg>Marriage Sessions</li>
    <li><svg viewBox="0 0 12 12"><path d="M1 6l3 3 7-7" fill="none" stroke="#222" stroke-width="2"/></svg>Custody Evaluation Sessions</li>
    <li><svg viewBox="0 0 12 12"><path d="M1 6l3 3 7-7" fill="none" stroke="#222" stroke-width="2"/></svg>Family Sessions</li>
    <li><svg viewBox="0 0 12 12"><path d="M1 6l3 3 7-7" fill="none" stroke="#222" stroke-width="2"/></svg>Testing Sessions</li>
    <li><svg viewBox="0 0 12 12"><path d="M1 6l3 3 7-7" fill="none" stroke="#222" stroke-width="2"/></svg>Phone Sessions</li>
    <li><svg viewBox="0 0 12 12"><path d="M1 6l3 3 7-7" fill="none" stroke="#222" stroke-width="2"/></svg>Weekend / Holiday Sessions</li>
  </ul>
  <span class="get-started">Get Started</span>
</section>

<section class="video abs" role="img" aria-label="Blue-toned photo of a distressed woman in a session, video placeholder">
  <p>Lorem ipsum dolor sit amet, consectetu</p>
  <div class="play"><svg viewBox="0 0 18 18"><path d="M4 2l12 7-12 7z" fill="#4f90c6"/></svg></div>
  <h3>WATCH VIDEO</h3>
</section>

<h2 class="script-title expertise-title abs">My <span>Expertise</span></h2>
<div class="title-rule expertise-rule abs"></div>

<div class="card c1 r1 abs"><svg class="ico" viewBox="0 0 54 54" fill="#2a2a2a"><path d="M27 47C10 34 4 26 4 17 4 10 9 5 16 5c5 0 9 3 11 7 2-4 6-7 11-7 7 0 12 5 12 12 0 9-6 17-23 30z"/></svg><h3>DATING</h3><p>Lorem ipsum dolor sit amet, consectetuer adipiscing elit, sed diam nonummy nibh</p><span class="corner"></span><span class="plus">+</span></div>
<div class="card c2 r1 abs"><svg class="ico" viewBox="0 0 54 54" fill="#2a2a2a"><circle cx="19" cy="9" r="5"/><circle cx="35" cy="9" r="5"/><rect x="15" y="16" width="8" height="18" rx="2"/><path d="M35 16l-7 18h14z"/><rect x="16" y="34" width="2.5" height="14"/><rect x="19.5" y="34" width="2.5" height="14"/><rect x="32" y="34" width="2.5" height="14"/><rect x="36" y="34" width="2.5" height="14"/></svg><h3>MARRIAGE</h3><p>Lorem ipsum dolor sit amet, consectetuer adipiscing elit, sed diam nonummy nibh</p><span class="corner"></span><span class="plus">+</span></div>
<div class="card c3 r1 abs"><svg class="ico" viewBox="0 0 54 54" fill="#2a2a2a"><rect x="22" y="6" width="28" height="22" fill="none" stroke="#2a2a2a" stroke-width="3"/><circle cx="12" cy="14" r="5"/><rect x="6" y="21" width="12" height="16"/><rect x="6" y="37" width="5" height="12"/><rect x="13" y="37" width="5" height="12"/><path d="M36 28l-5 20M36 28l5 20" stroke="#2a2a2a" stroke-width="2.5"/></svg><h3>PARENTING &amp; PROFESSIONAL</h3><p>Lorem ipsum dolor sit amet, consectetuer adipiscing elit, sed diam nonummy nibh</p><span class="corner"></span><span class="plus">+</span></div>
<div class="card c4 r1 abs"><svg class="ico" viewBox="0 0 54 54" fill="#2a2a2a"><circle cx="16" cy="11" r="6"/><circle cx="38" cy="11" r="6"/><circle cx="14" cy="36" r="11"/><circle cx="40" cy="36" r="11"/><path d="M9 36h8M13 32l-4 4 4 4M45 36h-8M41 32l4 4-4 4" stroke="#fff" stroke-width="2.5" fill="none"/></svg><h3>RELATIONSHIPS</h3><p>Lorem ipsum dolor sit amet, consectetuer adipiscing elit, sed diam nonummy nibh</p><span class="corner"></span><span class="plus">+</span></div>

<div class="card c1 r2 abs"><svg class="ico" viewBox="0 0 54 54" fill="#2a2a2a"><circle cx="30" cy="10" r="6"/><path d="M26 18l-10 16 6 2 8-10 2 10-10 12 4 3 12-14-4-16z"/></svg><h3>DEPRESSION &amp; ANXIETY ISSUES</h3><p>Lorem ipsum dolor sit amet, consectetuer adipiscing elit, sed diam nonummy nibh</p><span class="corner"></span><span class="plus">+</span></div>
<div class="card c2 r2 abs"><svg class="ico" viewBox="0 0 54 54" fill="#2a2a2a"><path d="M2 12c8-4 16-4 24 0v10c0 10-5 16-12 16S2 32 2 22z"/><path d="M28 16c8-4 16-4 24 0v10c0 10-5 16-12 16s-12-6-12-16z"/><circle cx="9" cy="20" r="2.5" fill="#e6e6e6"/><circle cx="19" cy="20" r="2.5" fill="#e6e6e6"/><circle cx="35" cy="24" r="2.5" fill="#e6e6e6"/><circle cx="45" cy="24" r="2.5" fill="#e6e6e6"/></svg><h3>PERSONALITY DISORDERS</h3><p>Lorem ipsum dolor sit amet, consectetuer adipiscing elit, sed diam nonummy nibh</p><span class="corner"></span><span class="plus">+</span></div>
<div class="card c3 r2 abs"><svg class="ico" viewBox="0 0 54 54" fill="#2a2a2a"><circle cx="27" cy="9" r="5"/><rect x="21" y="16" width="12" height="18"/><rect x="22" y="34" width="4" height="15"/><rect x="28" y="34" width="4" height="15"/><path d="M8 18h38" stroke="#2a2a2a" stroke-width="2.5"/><path d="M4 30l5-12 5 12zM40 30l5-12 5 12z"/></svg><h3>DIVORCE MEDIATION</h3><p>Lorem ipsum dolor sit amet, consectetuer adipiscing elit, sed diam nonummy nibh</p><span class="corner"></span><span class="plus">+</span></div>
<div class="card c4 r2 abs"><svg class="ico" viewBox="0 0 54 54" fill="#2a2a2a"><circle cx="27" cy="22" r="6"/><path d="M17 48c0-12 4-18 10-18s10 6 10 18z"/><circle cx="12" cy="10" r="3"/><circle cx="27" cy="5" r="3"/><circle cx="42" cy="10" r="3"/><circle cx="10" cy="24" r="3"/><circle cx="44" cy="24" r="3"/></svg><h3>LIFE MANAGEMENT</h3><p>Lorem ipsum dolor sit amet, consectetuer adipiscing elit, sed diam nonummy nibh</p><span class="corner"></span><span class="plus">+</span></div>

<section class="radio abs"></section>
<h2 class="script-title radio-title abs">Radio <span>Conversations</span></h2>
<div class="title-rule radio-rule abs"></div>
<svg class="radio-arrow abs" style="left:76px" viewBox="0 0 16 28"><path d="M13 2L3 14l10 12" fill="none" stroke="#aaa" stroke-width="2"/></svg>
<svg class="radio-arrow abs" style="left:1110px" viewBox="0 0 16 28"><path d="M3 2l10 12L3 26" fill="none" stroke="#aaa" stroke-width="2"/></svg>
<p class="quote abs"><span class="quote-mark">“</span>Lorem ipsum dolor sit amet, consectetuer adipiscing elit, sed diam nonummy nibh euismod tincidunt ut laoreet dolore magna aliquam erat volutpat. Ut wisi enim ad minim veniam, quis nostrud exerci tation ullamcorper suscipit lobortis nisl ut aliquip ex ea commodo consequat. Duis autem vel eum iriure.</p>
<div class="quote-name abs">Evan Marlow</div>

<footer class="footer abs" role="img" aria-label="Dark street map of the practice neighborhood"></footer>
<div class="donate abs">A portion of all revenue is donated to <span class="badge"></span><span class="badge"></span></div>
<div class="foot-row f-addr abs"><svg viewBox="0 0 20 20" fill="#fff"><path d="M10 1a6 6 0 0 0-6 6c0 5 6 12 6 12s6-7 6-12a6 6 0 0 0-6-6z"/><circle cx="10" cy="7" r="2.3" fill="#333"/></svg>418 Larkspur Avenue, Suite 210 Harbor Point, CA 90000</div>
<div class="foot-row f-phone abs"><svg viewBox="0 0 20 20" fill="#fff"><path d="M5 1l3 5-2 2c1 2 3 4 5 5l2-2 5 3-2 4C8 18 2 11 2 4z"/></svg>(555) 214 3089</div>
<div class="foot-row f-mail abs"><svg viewBox="0 0 20 20"><rect x="1" y="4" width="18" height="12" fill="#fff"/><path d="M1 4l9 7 9-7" fill="none" stroke="#333" stroke-width="1.5"/></svg>mk@drkalvoric.com</div>
<div class="copyright abs">Copyright 2016 Dr. Mara K. Kalvoric. All Right Reserved</div>

</body>
</html>
```